Project Overview: Website Redesign for Brovanta
We are looking to redesign our current website, www.brovantausa.example, to better match the style and functionality of these reference sites:
Quenrix Health
ZMD Hopwell
Key Requirements: Modern, Clean Design:
The site should have a professional and clean layout with clear messaging about our services.
Visual Elements: Use strong visuals like images, icons, or illustrations to support text and engage visitors.
Clear Service Breakdown: Easily digestible sections explaining what Brovanta offers, similar to the service explanations on the reference sites.
User-Friendly Navigation: Simple, intuitive navigation with visible CTAs (e.g., "Learn More," "Get Started").
Trust-Building Features: Incorporate trust elements like client logos, testimonials, or success stories to build credibility.
Mobile-Responsive:
Ensure the website is fully responsive and looks great on all devices (desktop, tablet, mobile).
SEO Optimization:
Deliverables: Fully functional website with modern design.
All content will be provided, but we may need help with imagery or layout recommendations.
Responsive design and mobile optimization.
We are looking for a clean, modern, and easy-to-navigate site that reflects the professionalism of our brand.

```html
<!DOCTYPE html>
<html lang="en">
<head>
<meta charset="utf-8">
<title>Brovanta — Medical Food for Sickle Cell Disease</title>
<link rel="stylesheet" href="https://fonts.googleapis.com/css2?family=Archivo+Black&family=Roboto:wght@400;500;700&display=swap">
<style>
:root{
  --red:#b5292f;
  --red-dark:#9e2328;
  --pink:#fbeaea;
  --pink-soft:#f7dcdc;
  --ink:#111;
  --text:#333;
  --muted:#555;
  --white:#fff;
  --footer:#0e0e0e;
  --display:"Archivo Black", sans-serif;
  --body:"Roboto", Arial, sans-serif;
}
*{box-sizing:border-box;margin:0;padding:0}
html,body{width:1200px;height:3984px;overflow:hidden}
body{font-family:var(--body);color:var(--text);background:var(--white);position:relative}
a{color:inherit;text-decoration:none}
.abs{position:absolute}

/* header */
.site-header{position:absolute;left:0;top:0;width:1200px;height:100px;background:var(--white);box-shadow:0 2px 6px rgba(0,0,0,.06);z-index:2}
.topbar{position:absolute;right:0;top:0;width:810px;height:42px;background:var(--red);border-bottom-left-radius:40px;display:flex;align-items:center;gap:70px;padding-left:90px;color:var(--white);font-weight:700;font-size:15px}
.topbar span{display:flex;align-items:center;gap:12px}
.topbar svg{width:26px;height:26px}
.brand{position:absolute;left:110px;top:18px;font-family:var(--body);font-weight:500;font-size:46px;color:var(--red);letter-spacing:1px}
.main-nav{position:absolute;left:402px;top:61px;display:flex;gap:25px;font-size:15px;color:#222}
.main-nav .active{color:var(--red);font-weight:500}

/* hero */
.hero{position:absolute;left:0;top:100px;width:1200px;height:647px;background:linear-gradient(90deg,#fdf1f1 0%,#fbecec 45%,#f3e3de 100%);overflow:hidden}
.hero-photo{position:absolute;left:640px;top:0;width:560px;height:647px;background:linear-gradient(160deg,#e9d6cd 0%,#d8bfb2 45%,#c9b3a8 100%)}
.hero-ring{position:absolute;left:690px;top:88px;width:330px;height:330px;border-radius:50%;background:var(--pink-soft)}
.hero h1{position:absolute;left:110px;top:100px;font-family:var(--display);font-size:44px;line-height:56px;color:var(--ink);font-weight:400}
.hero h1 .light{font-family:var(--body);font-weight:400}
.hero h2{position:absolute;left:108px;top:273px;width:500px;font-family:var(--body);font-weight:700;font-size:26px;line-height:38px;color:var(--red);letter-spacing:.5px}
.hero p{position:absolute;left:110px;top:362px;width:470px;font-size:15px;line-height:31px;color:#222}
.btn{display:inline-flex;align-items:center;justify-content:center;background:var(--red);color:var(--white);font-weight:700;font-size:16px;border-radius:3px}
.hero .btn{position:absolute;left:110px;top:438px;width:140px;height:46px}
.dots{position:absolute;left:110px;top:517px;display:flex;gap:9px;align-items:center}
.dots i{width:9px;height:9px;border-radius:50%;background:#bbb}
.dots i:first-child{width:12px;height:12px;background:var(--red)}
.dots svg{margin-left:30px}

/* offers */
.offers{position:absolute;left:0;top:747px;width:1200px;height:804px;background:var(--red);color:var(--white)}
.offers-photo{position:absolute;left:0;top:0;width:1200px;height:804px;background:radial-gradient(ellipse at 35% 55%,rgba(120,20,24,.35),rgba(181,41,47,0) 60%)}
.sec-title{font-family:var(--display);font-weight:400;font-size:36px}
.sec-title .light{font-family:var(--body);font-weight:400}
.underline{display:block;width:46px;height:3px;background:var(--red)}
.offers .sec-title{position:absolute;left:112px;top:80px}
.offers .underline{position:absolute;left:112px;top:138px;background:var(--white)}
.offers .intro{position:absolute;left:111px;top:157px;width:880px;font-size:15px;font-weight:500;line-height:31px}
.offer{position:absolute;left:111px;width:900px;height:100px}
.offer .ico{position:absolute;left:0;top:0;width:90px;height:90px;border-radius:50%;background:var(--white);display:flex;align-items:center;justify-content:center}
.offer h3{position:absolute;left:117px;top:-2px;font-size:17px;font-weight:700}
.offer p{position:absolute;left:117px;top:30px;width:720px;font-size:14.5px;line-height:31px}
.offers .btn{position:absolute;left:532px;top:666px;width:140px;height:46px;background:var(--white);color:var(--red);font-size:15px}

/* about */
.about{position:absolute;left:0;top:1551px;width:1200px;height:609px}
.about .sec-title{position:absolute;left:110px;top:94px;color:var(--ink)}
.about .underline{position:absolute;left:112px;top:143px}
.about p{position:absolute;left:110px;top:160px;width:470px;font-size:14.5px;line-height:31px;color:#333}
.about .btn{position:absolute;left:110px;top:459px;width:140px;height:46px;font-size:15px}
.about-ring{position:absolute;left:707px;top:116px;width:380px;height:380px;border-radius:50%;background:var(--pink-soft)}
.about-photo{position:absolute;left:733px;top:142px;width:328px;height:328px;border-radius:50%;background:linear-gradient(150deg,#8a6a4a,#4c3a2c 60%,#6d5642)}
.about-pack{position:absolute;left:623px;top:289px;width:190px;height:204px;background:linear-gradient(135deg,#ffffff,#eeeaea);box-shadow:0 8px 18px rgba(0,0,0,.18)}

/* services */
.services{position:absolute;left:0;top:2160px;width:1200px;height:618px;background:var(--pink)}
.center-title{position:absolute;left:0;width:1200px;text-align:center;color:var(--ink)}
.center-line{position:absolute;left:577px}
.services .center-title{top:76px}
.services .center-line{top:126px}
.card{position:absolute;top:210px;width:304px;height:320px;background:var(--white);box-shadow:0 2px 8px rgba(0,0,0,.08);text-align:center}
.card .badge{position:absolute;left:94px;top:-48px;width:116px;height:116px}
.card h3{position:absolute;left:0;top:97px;width:100%;font-size:20px;font-weight:500;color:var(--ink)}
.card p{position:absolute;left:22px;top:133px;width:260px;font-size:14px;line-height:31px;color:#444}
.card .more{position:absolute;left:0;top:270px;width:100%;font-size:15px;font-weight:700;color:var(--red)}
.card.dark .more{color:var(--ink)}

/* partners */
.partners .center-title{top:2860px}
.partners .center-line{top:2928px}
.partner{position:absolute;top:2960px;height:90px;background:#d6d6d6}

/* testimonials */
.testimonials .center-title{top:3100px}
.testimonials .center-line{top:3168px}
.quote-card{position:absolute;top:3208px;width:304px;height:217px;background:var(--white);box-shadow:0 2px 8px rgba(0,0,0,.1)}
.quote-card .mark{position:absolute;left:16px;top:-4px;font-family:Georgia,serif;font-size:70px;color:#ddd;line-height:1}
.quote-card p{position:absolute;left:18px;top:30px;width:276px;font-size:17px;line-height:26px;color:#333;text-align:justify}
.quote-card .avatar{position:absolute;left:24px;top:194px;width:68px;height:68px;background:linear-gradient(160deg,#cfcfcf,#8a8a8a)}
.quote-card .name{position:absolute;left:106px;top:222px;font-size:15px;letter-spacing:1px;color:var(--red)}
.arrow{position:absolute;top:3316px;width:32px;height:32px;border:1.5px solid #999;border-radius:50%}

/* footer */
.site-footer{position:absolute;left:0;top:3544px;width:1200px;height:440px;background:var(--footer);color:var(--white)}
.site-footer h4{position:absolute;top:72px;font-size:22px;font-weight:700}
.links{position:absolute;top:110px;list-style:none;font-size:15px;line-height:31px}
.links li{display:flex;align-items:center;gap:12px}
.contact{position:absolute;left:532px;list-style:none;font-size:15px}
.contact li{position:absolute;left:0;width:300px;display:flex;align-items:center;gap:14px;white-space:nowrap}
.contact .dot{width:36px;height:36px;border-radius:50%;background:var(--red);display:flex;align-items:center;justify-content:center;flex:none}
.news-text{position:absolute;left:827px;top:120px;width:290px;font-size:15px;line-height:31px}
.news-field{position:absolute;left:831px;top:192px;width:270px;height:32px;border-bottom:1px solid #ccc;font-size:15px}
.site-footer .btn{position:absolute;left:835px;top:253px;width:137px;height:52px;font-size:17px}
.rule{position:absolute;left:98px;top:378px;width:1004px;height:1px;background:#555}
.copy{position:absolute;left:0;top:395px;width:1200px;text-align:center;font-size:15px}
</style>
</head>
<body>

<header class="site-header">
  <div class="topbar">
    <span><svg viewBox="0 0 26 26"><circle cx="13" cy="13" r="13" fill="#fff"/><path d="M9 7l3 3-1.5 2a9 9 0 0 0 3.5 3.5l2-1.5 3 3-2 2C11 18 8 15 7 9z" fill="#b5292f"/></svg>Phone: +1 555 0100 2000</span>
    <span><svg viewBox="0 0 26 26"><circle cx="13" cy="13" r="13" fill="#fff"/><rect x="7" y="9" width="12" height="9" rx="1" fill="#b5292f"/><path d="M7 9l6 5 6-5" stroke="#fff" stroke-width="1.2" fill="none"/></svg>Email: info@brovanta.example</span>
  </div>
  <div class="brand">Brovanta</div>
  <nav class="main-nav">
    <a class="active">Home</a><a>About Us</a><a>About SCD</a><a>Healthcare Professionals</a><a>Patient Support</a><a>Nerivo Sciences</a>
  </nav>
</header>

<section class="hero">
  <div class="hero-photo" role="img" aria-label="Photo of a mother and daughter baking together in a kitchen"></div>
  <div class="hero-ring"></div>
  <h1>A Medical Food for the<br>Dietary Management<br><span class="light">of Sickle Cell</span></h1>
  <h2>Disease in Pediatric and Adult Patients.</h2>
  <p>BROVANTA was designed to provide this fatty acid used in these trials, in a safe, good tasting, easy to administer oral formulation.</p>
  <a class="btn">Get Started</a>
  <div class="dots"><i></i><i></i><i></i>
    <svg width="60" height="10" viewBox="0 0 60 10"><path d="M1 5h14M1 5l4-3M1 5l4 3" stroke="#999" fill="none"/><path d="M30 5h16M46 5l-4-3M46 5l-4 3" stroke="#111" stroke-width="2" fill="none"/></svg>
  </div>
</section>

<section class="offers">
  <div class="offers-photo" role="img" aria-label="Faint background photo of a family preparing food"></div>
  <h2 class="sec-title">What Brovanta <span class="light">offers</span></h2>
  <span class="underline"></span>
  <p class="intro">In clinical trials (2,3) conducted under a US Investigational New Drug Application, patients who consume high levels of DHA and see a significant increase in DHA blood levels.</p>

  <div class="offer" style="top:243px">
    <div class="ico"><svg width="46" height="46" viewBox="0 0 46 46"><path d="M8 20h26v6a13 13 0 0 1-26 0z" fill="#b5292f"/><path d="M34 22h4a3 3 0 0 1 0 6h-4" stroke="#b5292f" stroke-width="2.5" fill="none"/><rect x="6" y="38" width="30" height="3" rx="1.5" fill="#b5292f"/><path d="M16 8v8M22 6v10M28 8v8" stroke="#b5292f" stroke-width="2"/></svg></div>
    <h3>Fat malabsorption is a top contributor to digestive/GI problems.</h3>
    <p>Lorem ipsum dolor sit amet, consectetur adipiscing elit, sed do eiusmod tempor incididunt ut labore et dolore magna aliqua.</p>
  </div>
  <div class="offer" style="top:390px">
    <div class="ico"><svg width="46" height="46" viewBox="0 0 46 46"><path d="M23 24s-10-6-10-12a5 5 0 0 1 10-1 5 5 0 0 1 10 1c0 6-10 12-10 12z" fill="#b5292f"/><path d="M6 24c4 0 8 6 12 10v6M40 24c-4 0-8 6-12 10v6" stroke="#b5292f" stroke-width="3" fill="none"/><path d="M21 12h4M23 10v4" stroke="#fff" stroke-width="2"/></svg></div>
    <h3>GI-related health care expenses exceed $135 billion each year. 1</h3>
    <p>Lorem ipsum dolor sit amet, consectetur adipiscing elit, sed do eiusmod tempor incididunt ut labore et dolore magna aliqua.</p>
  </div>
  <div class="offer" style="top:537px">
    <div class="ico"><svg width="46" height="46" viewBox="0 0 46 46"><circle cx="14" cy="12" r="4" fill="#b5292f"/><circle cx="31" cy="9" r="4" fill="#b5292f"/><path d="M9 20h10v10H9zM26 16h10v14H26z" fill="#b5292f"/><path d="M10 30v10M18 30v10M28 30v10M34 30v10" stroke="#b5292f" stroke-width="3"/></svg></div>
    <h3>Other treatments can be complicated and less effective.</h3>
    <p>Lorem ipsum dolor sit amet, consectetur adipiscing elit, sed do eiusmod tempor incididunt ut labore et dolore magna aliqua.</p>
  </div>
  <a class="btn">Learn More</a>
</section>

<section class="about">
  <h2 class="sec-title">About <span class="light">Us</span></h2>
  <span class="underline"></span>
  <p>BROVANTA is a medical food specifically formulated to provide a consistent and highly bioavailable form of DHA, a major fatty acid found in Omega-3 fish oil, to replenish what is damaged by the hemoglobin mutation (HbS) found in sickle cell disease patients. In clinical trials (2,3) conducted under a US Investigational New Drug Application, patients who consume high levels of DHA and see a significant increase in DHA blood levels. An increase in DHA levels may impact the oxidative and inflammatory cascade leading to sickle cell pain crises or vaso-occlusive events.</p>
  <a class="btn">Learn More</a>
  <div class="about-ring"></div>
  <div class="about-photo" role="img" aria-label="Photo of a mother and two children sharing a meal"></div>
  <div class="about-pack" role="img" aria-label="Product carton image"></div>
</section>

<section class="services">
  <h2 class="sec-title center-title">Our <span class="light">Services</span></h2>
  <span class="underline center-line"></span>

  <article class="card" style="left:110px">
    <svg class="badge" viewBox="0 0 116 116"><path d="M20 58a38 38 0 0 1 76 0M96 58a38 38 0 0 1-76 0" stroke="#b5292f" stroke-width="1.5" fill="none" stroke-dasharray="90 30"/><path d="M10 58a48 48 0 0 1 96 0M106 58a48 48 0 0 1-96 0" stroke="#b5292f" stroke-width="1.5" fill="none" stroke-dasharray="60 90"/><circle cx="58" cy="58" r="30" fill="#b5292f"/><circle cx="58" cy="54" r="7" fill="none" stroke="#fff" stroke-width="2"/><path d="M46 74a12 12 0 0 1 24 0" stroke="#fff" stroke-width="2" fill="none"/></svg>
    <h3>Healthcare Professionals</h3>
    <p>BROVANTA is a medical food specifically formulated to provide a consistent and highly bioavailable form of DHA, a major fatty acid found in Omega-3 fish oil,</p>
    <a class="more">Learn More ➔</a>
  </article>
  <article class="card dark" style="left:447px">
    <svg class="badge" viewBox="0 0 116 116"><path d="M20 58a38 38 0 0 1 76 0M96 58a38 38 0 0 1-76 0" stroke="#111" stroke-width="1.5" fill="none" stroke-dasharray="90 30"/><path d="M10 58a48 48 0 0 1 96 0M106 58a48 48 0 0 1-96 0" stroke="#111" stroke-width="1.5" fill="none" stroke-dasharray="60 90"/><circle cx="58" cy="58" r="30" fill="#111"/><circle cx="50" cy="50" r="4" fill="#fff"/><path d="M45 58h10v14h-10z" fill="#fff"/><rect x="60" y="48" width="12" height="10" fill="none" stroke="#fff" stroke-width="2"/><path d="M66 58v14" stroke="#fff" stroke-width="2"/></svg>
    <h3>Patient Support</h3>
    <p>BROVANTA is a medical food specifically formulated to provide a consistent and highly bioavailable form of DHA, a major fatty acid found in Omega-3 fish oil,</p>
    <a class="more">Learn More ➔</a>
  </article>
  <article class="card" style="left:784px">
    <svg class="badge" viewBox="0 0 116 116"><path d="M20 58a38 38 0 0 1 76 0M96 58a38 38 0 0 1-76 0" stroke="#b5292f" stroke-width="1.5" fill="none" stroke-dasharray="90 30"/><path d="M10 58a48 48 0 0 1 96 0M106 58a48 48 0 0 1-96 0" stroke="#b5292f" stroke-width="1.5" fill="none" stroke-dasharray="60 90"/><circle cx="58" cy="58" r="30" fill="#b5292f"/><path d="M52 42h12M55 42v12l-8 16h22l-8-16V42" stroke="#fff" stroke-width="2" fill="none"/><path d="M50 66h16l3 4H47z" fill="#fff"/></svg>
    <h3>Nerivo Sciences</h3>
    <p>BROVANTA is a medical food specifically formulated to provide a consistent and highly bioavailable form of DHA, a major fatty acid found in Omega-3 fish oil,</p>
    <a class="more">Learn More ➔</a>
  </article>
</section>

<section class="partners">
  <h2 class="sec-title center-title">Our <span class="light">Partners</span></h2>
  <span class="underline center-line"></span>
  <div class="partner" style="left:112px;width:112px;border-radius:50%;width:90px;left:124px"></div>
  <div class="partner" style="left:282px;width:158px;border-radius:6px"></div>
  <div class="partner" style="left:494px;width:170px;border-radius:6px"></div>
  <div class="partner" style="left:717px;width:143px;border-radius:6px"></div>
  <div class="partner" style="left:913px;width:177px;border-radius:6px"></div>
</section>

<section class="testimonials">
  <h2 class="sec-title center-title">Client <span class="light">Testimonials</span></h2>
  <span class="underline center-line"></span>
  <span class="arrow" style="left:34px"></span>
  <span class="arrow" style="left:1134px"></span>
  <article class="quote-card" style="left:110px"><span class="mark">“</span><p>Sed ut perspiciatis unde omnis iste natus error sit voluptatem accuslore antiumerw doloremque laudantium, totam rem aperiam, eaque ipsa quae ab illo inventore..”</p><div class="avatar" role="img" aria-label="Client portrait"></div><span class="name">NAME HEADING</span></article>
  <article class="quote-card" style="left:447px"><span class="mark">“</span><p>Sed ut perspiciatis unde omnis iste natus error sit voluptatem accuslore antiumerw doloremque laudantium, totam rem aperiam, eaque ipsa quae ab illo inventore..”</p><div class="avatar" role="img" aria-label="Client portrait"></div><span class="name">NAME HEADING</span></article>
  <article class="quote-card" style="left:784px"><span class="mark">“</span><p>Sed ut perspiciatis unde omnis iste natus error sit voluptatem accuslore antiumerw doloremque laudantium, totam rem aperiam, eaque ipsa quae ab illo inventore..”</p><div class="avatar" role="img" aria-label="Client portrait"></div><span class="name">NAME HEADING</span></article>
</section>

<footer class="site-footer">
  <h4 style="left:110px">Quick Links</h4>
  <ul class="links" style="left:112px">
    <li>➔ About BROVANTA</li><li>➔ About SCD</li><li>➔ Healthcare Professionals</li><li>➔ Patient Support</li><li>➔ Nerivo Sciences</li>
  </ul>
  <h4 style="left:359px">Other Links</h4>
  <ul class="links" style="left:359px">
    <li>➔ FAQ</li><li>➔ Terms of Use</li><li>➔ Privacy Policy</li><li>➔ Support Links</li><li>➔ Conditions</li>
  </ul>
  <h4 style="left:532px">Contact Us</h4>
  <ul class="contact">
    <li style="top:122px"><span class="dot"><svg width="14" height="18" viewBox="0 0 14 18"><path d="M7 0a7 7 0 0 1 7 7c0 5-7 11-7 11S0 12 0 7a7 7 0 0 1 7-7z" fill="#fff"/><circle cx="7" cy="7" r="2.5" fill="#b5292f"/></svg></span>Company Name,United State.</li>
    <li style="top:183px"><span class="dot"><svg width="16" height="12" viewBox="0 0 16 12"><rect width="16" height="12" rx="1" fill="#fff"/><path d="M0 1l8 6 8-6" stroke="#b5292f" fill="none"/></svg></span>info@companyname.example</li>
    <li style="top:242px"><span class="dot"><svg width="16" height="16" viewBox="0 0 16 16"><path d="M3 1l3 3-1.5 2a9 9 0 0 0 4.5 4.5l2-1.5 3 3-2 2C6 13 3 10 1 3z" fill="#fff"/></svg></span>+1 555 0100 2000</li>
  </ul>
  <h4 style="left:827px">Sign Up To Our Newsletter</h4>
  <p class="news-text">Lorem ipsum dolor sit amet,consectetur adipiscing elit,adipiscing elit.</p>
  <div class="news-field">Email</div>
  <a class="btn">Subscribe</a>
  <div class="rule"></div>
  <p class="copy">©2025.Company Name.All Rights Reserved</p>
</footer>

</body>
</html>
```